Software allocation system needs a business card design

We need a business card designed for our software platform - www.tallivo.com.au

At the moment the logo and website is all black and white, we are happy for suggestions on implementing some colour throughout either the logo or business card.

Industry/Entity Type

Software

Font styles to use
Sans Serif

Colors

Designer to choose colors to be used in the design.

```html
<!DOCTYPE html>
<html lang="en">
<head>
<meta charset="utf-8">
<title>Tallivo Business Card</title>
<link rel="stylesheet" href="https://fonts.googleapis.com/css2?family=Josefin+Sans:wght@300;400&family=Arimo:wght@400;700&display=swap">
<style>
  :root {
    --bg: #2a1d1b;
    --card-black: #050505;
    --band-grey: #2b2b2b;
    --panel-light: #e9e9e9;
    --panel-shade: #d6d6d6;
    --ink-white: #f2f2f2;
    --ink-dark: #1c1c1c;
    --ink-soft: #bdbdbd;
  }
  * { box-sizing: border-box; margin: 0; padding: 0; }
  html, body { width: 1200px; height: 486px; overflow: hidden; }
  body {
    background: var(--bg);
    font-family: "Arimo", Arial, sans-serif;
    position: relative;
  }
  .card { position: absolute; background: var(--card-black); overflow: hidden; }

  /* Front */
  .card-front {
    left: 150px; top: 128px; width: 420px; height: 232px;
    display: flex; align-items: center; justify-content: center; gap: 16px;
  }
  .brand-dot { width: 34px; height: 34px; border-radius: 50%; background: var(--ink-white); }
  .brand-name {
    font-family: "Josefin Sans", sans-serif; font-weight: 300;
    font-size: 52px; letter-spacing: 6px; color: var(--ink-white); line-height: 1;
  }

  /* Back */
  .card-back { left: 650px; top: 44px; width: 236px; height: 394px; }
  .back-top {
    position: absolute; left: 0; top: 0; width: 100%; height: 150px;
    background: linear-gradient(90deg, var(--panel-light) 60%, var(--panel-shade));
  }
  .back-top svg { position: absolute; inset: 0; }
  .back-brand {
    position: absolute; left: 18px; top: 50px;
    display: flex; align-items: center; gap: 8px;
  }
  .back-brand .brand-dot { width: 20px; height: 20px; background: var(--ink-dark); }
  .back-brand .brand-name { font-size: 30px; letter-spacing: 3px; color: var(--ink-dark); }
  .tagline {
    position: absolute; left: 18px; top: 88px; width: 210px;
    font-size: 6.5px; font-weight: 700; letter-spacing: 0.6px;
    color: var(--ink-dark); text-transform: uppercase;
  }
  .name-band {
    position: absolute; left: 0; top: 172px; width: 100%; height: 60px;
    background: var(--band-grey); text-align: right; padding: 12px 16px 0 0;
  }
  .person-name { font-size: 22px; color: var(--ink-white); line-height: 1; }
  .person-role { font-size: 10px; color: var(--ink-white); margin-top: 3px; }
  .contact-list { position: absolute; left: 16px; top: 246px; list-style: none; }
  .contact-list li {
    display: flex; align-items: flex-start; gap: 14px;
    font-size: 11px; color: var(--ink-white); line-height: 1.3; margin-bottom: 12px;
  }
  .contact-list svg { flex: none; width: 16px; height: 16px; fill: var(--ink-white); }
</style>
</head>
<body>
  <section class="card card-front" aria-label="Card front">
    <span class="brand-dot"></span>
    <span class="brand-name">TALLIVO</span>
  </section>

  <section class="card card-back" aria-label="Card back">
    <div class="back-top">
      <svg viewBox="0 0 236 150" preserveAspectRatio="none" aria-hidden="true">
        <polygon points="0,0 236,0 236,14 140,14 130,24 90,24 80,14 0,14" fill="#050505"/>
      </svg>
      <div class="back-brand">
        <span class="brand-dot"></span>
        <span class="brand-name">TALLIVO</span>
      </div>
      <p class="tagline">Planning &amp; compliance for heavy industry</p>
    </div>
    <svg style="position:absolute;left:0;top:148px" width="236" height="16" viewBox="0 0 236 16" aria-hidden="true">
      <polygon points="100,0 136,0 118,14" fill="#e9e9e9"/>
    </svg>

    <div class="name-band">
      <p class="person-name">Mara Quinn</p>
      <p class="person-role">Head Director</p>
    </div>

    <ul class="contact-list">
      <li>
        <svg viewBox="0 0 16 16" aria-hidden="true"><path d="M8 1a5 5 0 0 0-5 5c0 4 5 9 5 9s5-5 5-9a5 5 0 0 0-5-5zm0 7a2 2 0 1 1 0-4 2 2 0 0 1 0 4z"/></svg>
        <span>PO Box 217<br>Elm Ridge NSW 2099</span>
      </li>
      <li>
        <svg viewBox="0 0 16 16" aria-hidden="true"><path d="M1 6c0-2 3-3 7-3s7 1 7 3v1h-3V6H4v1H1zM3 8h10l1 6H2z"/></svg>
        <span>(Insert your number)</span>
      </li>
      <li>
        <svg viewBox="0 0 16 16" aria-hidden="true"><text x="0" y="13" font-size="15" font-family="Arial, sans-serif" fill="#f2f2f2">@</text></svg>
        <span>hello@tallivo.com.au</span>
      </li>
      <li>
        <svg viewBox="0 0 16 16" aria-hidden="true"><circle cx="8" cy="8" r="5"/></svg>
        <span>http://www.tallivo.com.au/</span>
      </li>
    </ul>
  </section>
</body>
</html>
```